Zolvana Stationary and Branding Documents

Corporate Identity Branding stationary needed for IT Recruiting Firm.

I already have a Logo, business cards and website. I need to get designs completed for the remaining corporate identity documents.

The documentation should use similar colors as my website and business card. The designs should modern and clean.

http://zolvanaworks.example/

Target Market(s)

Information Technology Industry

Industry/Entity Type

Information Technology

Colors
3377b5
0255a3
fbee3e
f78f20
f37122
33a6d7
000000
0592cd

Requirements
Must have
• Letter Head
• Folder Design
• PowerPoint Design
• Invoice
• Envelope
Nice to have
• Proposal
• Flyer
• Brochure
Should not have
• Logo
• Business Cards
• Website

```html
<!DOCTYPE html>
<html lang="en">
<head>
<meta charset="utf-8">
<title>Zolvana Letterhead</title>
<link href="https://fonts.googleapis.com/css2?family=Open+Sans:wght@400;700&display=swap" rel="stylesheet">
<style>
  :root {
    --backdrop: #dfe5f6;
    --paper: #f8f9fa;
    --brand-blue: #0255a3;
    --brand-navy: #134f8a;
    --brand-orange: #f37122;
    --accent-orange: #f78f20;
    --ink: #1f1f1f;
    --tile-peach: #f9e5d0;
    --tile-sand: #f5e4d6;
    --tile-stone: #ece1d2;
  }
  * { margin: 0; padding: 0; box-sizing: border-box; }
  html, body { width: 1200px; height: 784px; overflow: hidden; }
  body {
    background: var(--backdrop);
    font-family: "Open Sans", sans-serif;
    position: relative;
  }
  .letterhead {
    position: absolute;
    left: 345px;
    top: 32px;
    width: 510px;
    height: 720px;
    background: var(--paper);
    box-shadow: 0 4px 18px rgba(40, 60, 120, 0.18);
    overflow: hidden;
  }
  .letterhead__shapes {
    position: absolute;
    inset: 0;
    width: 100%;
    height: 100%;
  }
  .brand {
    position: absolute;
    top: 40px;
    right: 28px;
    display: flex;
    align-items: center;
    gap: 7px;
  }
  .brand__mark {
    width: 8px;
    height: 8px;
    background: var(--brand-orange);
  }
  .brand__name {
    font-weight: 700;
    font-size: 30px;
    line-height: 1;
    color: var(--brand-blue);
    letter-spacing: 0.5px;
  }
  .contact-bar {
    position: absolute;
    left: 14px;
    bottom: 10px;
    display: flex;
    align-items: center;
    gap: 5px;
    font-size: 8px;
    color: var(--ink);
    white-space: nowrap;
  }
  .contact-bar__item {
    display: flex;
    align-items: center;
    gap: 3px;
  }
  .contact-bar__icon {
    width: 7px;
    height: 7px;
    flex: none;
  }
</style>
</head>
<body>
  <main class="letterhead">
    <svg class="letterhead__shapes" viewBox="0 0 510 720" aria-hidden="true">
      <polygon class="corner-orange" points="318,0 510,0 510,74" fill="var(--brand-orange)"/>
      <polygon class="corner-orange-inner" points="330,0 510,0 510,60 350,4" fill="var(--accent-orange)" opacity="0.55"/>
      <polygon class="corner-blue" points="0,616 40,616 0,720" fill="var(--brand-navy)"/>
      <rect class="tile tile--one" x="78" y="588" width="82" height="74" rx="14" fill="var(--tile-peach)" transform="rotate(22 119 625)"/>
      <rect class="tile tile--two" x="228" y="600" width="82" height="74" rx="14" fill="var(--tile-sand)" transform="rotate(22 269 637)"/>
      <rect class="tile tile--three" x="462" y="592" width="82" height="74" rx="14" fill="var(--tile-stone)" transform="rotate(22 503 629)"/>
    </svg>

    <div class="brand">
      <span class="brand__mark"></span>
      <span class="brand__name">Zolvana</span>
    </div>

    <footer class="contact-bar">
      <span class="contact-bar__item">
        <svg class="contact-bar__icon" viewBox="0 0 10 10"><circle cx="5" cy="5" r="5" fill="var(--accent-orange)"/><path d="M5 2.2a1.8 1.8 0 0 0-1.8 1.8c0 1.4 1.8 3.6 1.8 3.6s1.8-2.2 1.8-3.6A1.8 1.8 0 0 0 5 2.2z" fill="#fff"/></svg>
        Four Harbor Plaza 210 Linden Avenue
      </span>
      <span class="contact-bar__item">
        <svg class="contact-bar__icon" viewBox="0 0 10 10"><circle cx="5" cy="5" r="5" fill="var(--accent-orange)"/><path d="M3.3 2.4l1 1.2-.5.7c.4.8 1 1.4 1.8 1.8l.7-.5 1.2 1-.5.9C5 7.4 2.6 5 2.4 3z" fill="#fff"/></svg>
        8005550147
      </span>
      <span class="contact-bar__item">
        <svg class="contact-bar__icon" viewBox="0 0 10 10"><circle cx="5" cy="5" r="5" fill="var(--accent-orange)"/><rect x="2.5" y="3.3" width="5" height="3.4" fill="none" stroke="#fff" stroke-width="0.8"/><path d="M2.5 3.3L5 5.2l2.5-1.9" fill="none" stroke="#fff" stroke-width="0.8"/></svg>
        info@zolvanaworks.example
      </span>
      <span class="contact-bar__item">
        <svg class="contact-bar__icon" viewBox="0 0 10 10"><circle cx="5" cy="5" r="5" fill="var(--accent-orange)"/><circle cx="5" cy="5" r="2.6" fill="none" stroke="#fff" stroke-width="0.8"/><path d="M2.4 5h5.2M5 2.4v5.2" stroke="#fff" stroke-width="0.6"/></svg>
        www.zolvanaworks.example
      </span>
    </footer>
  </main>
</body>
</html>
```